Micro Markets Vending business needs a web design

I purchased a logo through MarkHarbor and asked them to design my website but was told they couldn't and that I needed to contact you.
I was building a website through Plume using AI and liked what they had created verbiage-wise but I can't figure out how to finish it the way I would like it. Will send screen shots of what was written, and subsequently used in my slogan under my logo. Would like to use the colors in my logo for my website.
About the company:
RT Snackworks, LLC offers micro market vending machines. Swipe your card, open the doors, take what you want. Can be customized by size for the space, and items for sale within the machines. Pictures of the machines are attached as examples.
I don't need a Testimonials page right now since we are a new company, but will need to add one at some point.
I also like the idea of a contact us button, as shown in the last picture (although it says subscribe). We do not have any emails set up as of yet. Haven't figured out how to do that, but will.
Just let me know what files you need from MarkHarbor for my logo.
Target Market(s)
Apartment complexes, Buildings, Hotels, Gyms, etc
Industry/Entity Type
Vending Machines
Coding
Coded - Design and coding required
Number of Pages Required
1 page
Font styles to use
Other font styles liked:
- Your choice on font style that complements our logo font.
Look and feel
Each slider illustrates characteristics of the customer's brand and the style your logo design should communicate.

```html
<!DOCTYPE html>
<html lang="en">
<head>
<meta charset="utf-8">
<title>RT Snackworks – Homepage Options</title>
<link rel="stylesheet" href="https://fonts.googleapis.com/css2?family=Lato:ital,wght@0,400;0,700;0,900;1,400&display=swap">
<style>
:root{
  --ink:#0b1f10;
  --ink-2:#122a18;
  --green:#3cc22b;
  --green-soft:#7fdc6e;
  --sage:#dfe9e3;
  --sage-2:#c9dcd1;
  --sage-3:#97b2a4;
  --paper:#f1f2f1;
  --board:#000;
  --white:#fff;
  --muted:#b8c7bd;
}
*{box-sizing:border-box;margin:0;padding:0}
html,body{width:965px;height:1200px;overflow:hidden;background:var(--board);font-family:"Lato",sans-serif}
.board{position:relative;width:965px;height:1200px;overflow:hidden}

.option-label{position:absolute;white-space:nowrap;font-size:18px;color:var(--white);transform:translate(-50%,-50%) rotate(-90deg);letter-spacing:.2px}
.option-label b{color:var(--green);font-weight:400}

.page{position:absolute;top:0;width:324px;height:1200px;background:var(--paper);overflow:hidden}
.page > section,.page > header,.page > footer,.page > div.strip{position:absolute;left:0;width:324px}

/* top bar */
.topbar{top:0;height:17px;background:#eef2ef;font-size:3.4px;color:#43524a}
.topbar .hours{position:absolute;left:46px;top:7px}
.topbar nav{position:absolute;top:7px;display:flex;gap:6px}

/* header */
.masthead{top:17px;height:28px;background:var(--ink);z-index:2}
.brand{position:absolute;left:50px;top:7px;display:flex;align-items:center;gap:4px}
.brand-mark{width:12px;height:12px;border:1.2px solid var(--green);}
.brand-name{font-size:8px;font-weight:700;letter-spacing:1.4px;color:var(--white)}
.tools{position:absolute;left:218px;top:9px;width:61px;height:9px;background:var(--white);display:flex;align-items:center;padding:0 3px;gap:3px}
.tools .search{flex:1;height:5px;border:.4px solid #bbb;font-size:2.4px;color:#999;padding-left:2px;line-height:4.5px}
.tools svg{width:5px;height:5px}

/* hero */
.hero{top:45px;height:159px;background:var(--ink)}
.hero-photo{position:absolute;left:116px;top:0;width:208px;height:159px;background:linear-gradient(90deg,var(--ink) 0%,#3a4a3c 25%,#6f6a5c 55%,#4c4a42 100%)}
.hero-copy{position:absolute;left:52px;top:41px;color:var(--white)}
.hero .eyebrow{font-size:5px;font-weight:700;letter-spacing:.2px}
.hero h1{font-size:15.5px;font-weight:900;line-height:15.5px;margin-top:1.5px}
.hero .slogan{font-size:6.6px;font-style:italic;color:var(--green);margin-top:3px;letter-spacing:.3px}
.hero p{font-size:4.4px;line-height:7px;width:112px;margin-top:4px}

/* machines */
.machines{top:204px;height:203px;background:var(--sage)}
.section-title{position:absolute;left:0;width:324px;text-align:center;font-weight:400;color:#1a1a1a}
.section-title em{font-style:normal;color:var(--green)}
.machines .section-title{top:8px;font-size:14.5px}
.shape-left{position:absolute;left:0;top:24px;width:107px;height:134px;background:var(--sage-3);border-top-right-radius:30px}
.shape-right{position:absolute;right:0;top:60px;width:102px;height:112px;background:var(--sage-2);border-bottom-left-radius:34px}
.machine{position:absolute}
.machine-compact{left:82px;top:39px;width:49px;height:129px;background:linear-gradient(180deg,#1b1b1b,#3b3f45 50%,#111)}
.machine-standard{left:152px;top:55px;width:115px;height:100px;background:linear-gradient(180deg,#222,#4a5560 50%,#141414)}
.machine-name{position:absolute;top:182px;font-size:6px;font-weight:700;letter-spacing:.4px;color:#1a3a24;transform:translateX(-50%)}

/* about */
.about{top:407px;height:147px;background:#d4e2d9}
.about-photo{position:absolute;left:155px;top:0;width:169px;height:147px;background:linear-gradient(90deg,#d4e2d9 0%,#a9b3b0 25%,#8c8f8c 60%,#5d6060 100%)}
.about-copy{position:absolute;left:52px;top:18px}
.about h2{font-size:14px;font-weight:400;line-height:14.5px;color:#1a1a1a}
.about h2 span{display:block;color:var(--green);font-size:14.5px}
.about p{font-size:4.4px;line-height:6.3px;width:98px;margin-top:7px;color:#2d3a32}

/* why */
.why{top:554px;height:147px;background:#141615}
.why-photo{position:absolute;left:0;top:0;width:324px;height:147px;background:linear-gradient(90deg,#1d221f,#2a2c2a 50%,#1b1d1c)}
.why-machine{position:absolute;left:55px;top:-14px;width:81px;height:169px;background:linear-gradient(180deg,#121212,#2f3e47 40%,#0c0c0c);z-index:3}
.why-copy{position:absolute;left:151px;top:10px;color:var(--white)}
.why h2{font-size:14px;font-weight:400;line-height:14.5px}
.why h2 span{display:block;color:var(--green)}
.reason{position:absolute;left:0;width:160px}
.reason svg{position:absolute;left:0;top:0;width:18px;height:18px}
.reason h3{position:absolute;left:23px;top:0;font-size:6px;font-weight:400;white-space:nowrap}
.reason h3 i{color:var(--green);font-size:4.6px}
.reason p{position:absolute;left:23px;top:8px;width:86px;font-size:3.1px;line-height:4px;color:#ddd}

/* inventory */
.inventory{top:701px;height:167px;background:var(--paper)}
.choc{position:absolute;left:0;top:6px;width:58px;height:66px;background:radial-gradient(circle at 40% 40%,#5a3a26,#3b2417 60%,transparent 72%)}
.chips{position:absolute;left:230px;top:121px;width:94px;height:63px;background:radial-gradient(ellipse at 50% 50%,#f3c93b,#e9b22a 50%,transparent 72%);z-index:1}
.inventory .section-title{top:28px;font-size:11.5px}
.tiles{position:absolute;left:47px;top:50px;display:grid;grid-template-columns:repeat(4,54px);gap:4px 4.5px}
.tile{height:37px;background:var(--white);border:.5px solid #ddd;position:relative}
.tile .pic{position:absolute;left:6px;top:3px;right:6px;height:22px;background:linear-gradient(135deg,#d9453a,#f0b33a 50%,#2b63c7)}
.tile:nth-child(4n+2) .pic{background:linear-gradient(135deg,#f28a1c,#e9d44a)}
.tile:nth-child(4n+3) .pic{background:linear-gradient(135deg,#2f55b8,#d8443a)}
.tile:nth-child(4n) .pic{background:linear-gradient(135deg,#1e3e8c,#c8ccd4,#c0202a)}
.tile .cap{position:absolute;left:0;right:0;bottom:0;height:7px;background:#222;color:#fff;font-size:2.8px;line-height:7px;padding-left:4px}
.inventory .note{position:absolute;top:142px;left:0;width:324px;text-align:center;font-size:3.9px;color:#222}

/* faq */
.faq{top:868px;height:106px;background:var(--paper)}
.faq .section-title{top:4px;font-size:11.5px}
.q{position:absolute;height:13px;background:var(--white);box-shadow:0 .5px 2px rgba(0,0,0,.12);font-size:2.8px;color:#222;padding:0 6px 0 8px;display:flex;align-items:center;justify-content:space-between}
.q::after{content:"⌄";font-size:3px;color:#666}
.q.open{height:35px;flex-direction:column;align-items:flex-start;justify-content:flex-start;padding-top:5px;border-left:1px solid var(--green);box-shadow:none;background:transparent}
.q.open::after{display:none}
.q.open p{margin-top:3px;font-size:2.5px;line-height:3.6px;color:#555;padding-left:4px}
.q.left{left:47px;width:102px}
.q.right{left:166px;width:111px}

/* contact */
.contact{top:974px;height:143px;background:var(--paper)}
.contact-photo{position:absolute;left:0;top:14px;width:171px;height:116px;background:linear-gradient(120deg,#8a7a66,#b69b7a 40%,#6b5e50 75%,#3e3a35)}
.contact h2{position:absolute;left:180px;top:22px;font-size:11.5px;font-weight:400;line-height:12.5px;color:#1a1a1a}
.contact h2 span{display:block;color:var(--green)}
.field{position:absolute;height:9.5px;background:var(--sage-2);font-size:2.6px;color:#fff;padding:3px 3px}
.submit{position:absolute;left:180px;top:112px;width:42px;height:13px;background:var(--green);color:#fff;font-size:6px;font-weight:700;text-align:center;line-height:13px}

/* footer */
.site-footer{top:1117px;height:68px;background:var(--ink);color:var(--white)}
.site-footer h4{position:absolute;top:13px;font-size:4.2px;font-weight:700}
.site-footer .contact-list{position:absolute;left:49px;top:23px;font-size:2.9px;line-height:8px}
.site-footer .contact-list div{display:flex;align-items:center;gap:2px}
.site-footer .contact-list svg{width:4px;height:4px}
.site-footer .links{position:absolute;left:128px;top:23px;font-size:2.9px;line-height:6px}
.site-footer .signup{position:absolute;left:209px;top:11px;width:58px}
.signup h4{position:static;margin-bottom:7px}
.signup p{font-size:3px;line-height:4px}
.signup .email{margin-top:4px;height:9px;background:var(--sage-2);font-size:2.5px;color:#fff;padding:3px 3px}
.signup .send{margin-top:4px;height:10px;background:var(--green);font-size:3.4px;font-weight:700;text-align:center;line-height:10px}
.strip{top:1185px;height:15px;background:#d7e4dc;text-align:center;font-size:3.3px;line-height:15px;color:#333}
</style>
</head>
<body>
<main class="board">

  <div class="option-label" style="left:67px;top:337px"><b>Option #1</b> &nbsp;( Remove the login button . Also remove the “Blog” from header)</div>
  <div class="option-label" style="left:531px;top:458px"><b>Option #2</b> &nbsp;( Change the login button to a search button . Also Change the “Blog” from header to Inventory)</div>

  <!-- ================= OPTION 1 ================= -->
  <article class="page" style="left:107px">
    <header class="topbar">
      <span class="hours">Mon - Fri: 8AM - 5PM &nbsp;| &nbsp;Order by phone: (555) 014-2290</span>
      <nav style="left:207px"><span>About Us</span><span>Services</span><span>FAQs</span><span>Contact Us</span></nav>
    </header>
    <header class="masthead">
      <div class="brand"><span class="brand-mark"></span><span class="brand-name">RT SNACKWORKS, LLC</span></div>
    </header>
    <section class="hero">
      <div class="hero-photo" role="img" aria-label="Customer choosing a drink from an open micro market cooler"></div>
      <div class="hero-copy">
        <div class="eyebrow">DISCOVER OUR RANGE</div>
        <h1>Welcome to<br>RT Snackworks</h1>
        <div class="slogan">where convenience meets customization.</div>
        <p>Our micro market vending machines offer a variety of snacks and drinks tailored to your preferences. Swipe your credit card, open the doors, and indulge in what you desire.</p>
      </div>
    </section>
    <section class="machines">
      <div class="shape-left"></div><div class="shape-right"></div>
      <h2 class="section-title">Our <em>Machines</em></h2>
      <div class="machine machine-compact" role="img" aria-label="Compact combo single-door cooler stocked with snacks and drinks"></div>
      <div class="machine machine-standard" role="img" aria-label="Standard combo double-door cooler stocked with snacks and drinks"></div>
      <span class="machine-name" style="left:101px">COMPACT COMBO</span>
      <span class="machine-name" style="left:216px">STANDARD COMBO</span>
    </section>
    <section class="about">
      <div class="about-photo" role="img" aria-label="Micro market installation with shelves and a glass-door cooler"></div>
      <div class="about-copy">
        <h2>About<span>RT SNACKWORKS</span></h2>
        <p>At RT Snackworks, we are dedicated to revolutionizing the vending experience. Our mission is to provide a convenient way for you to access your favorite snacks and drinks in a hassle-free manner. With a focus on customer satisfaction, we ensure that our products are always fresh and our machines are well-maintained. Experience the future of vending with RT Snackworks, LLC.</p>
      </div>
    </section>
    <section class="why">
      <div class="why-photo" role="img" aria-label="Dim store interior with stocked shelves"></div>
      <div class="why-machine" role="img" aria-label="Glass-door drinks cooler"></div>
      <div class="why-copy">
        <h2>Why<span>Choose Us</span></h2>
        <div class="reason" style="top:33px">
          <svg viewBox="0 0 18 18" fill="none" stroke="#fff" stroke-width=".8"><rect x="1" y="2" width="10" height="12"/><path d="M1 6h10M1 10h10"/><circle cx="13" cy="13" r="4" stroke="#3cc22b"/><path d="M11 13l1.5 1.5L15 12" stroke="#3cc22b"/></svg>
          <h3>Quality Products - <i>Fresh &amp; Varied Selections</i></h3>
          <p>Our vending machines are stocked with a diverse range of snacks and drinks, ensuring that there's something for everyone. We source only the freshest products for your enjoyment.</p>
        </div>
        <div class="reason" style="top:66px">
          <svg viewBox="0 0 18 18" fill="none" stroke="#fff" stroke-width=".8"><circle cx="8" cy="7" r="5.5" stroke="#3cc22b"/><path d="M5.5 7l2 2 3-3.5" stroke="#3cc22b"/><path d="M9 12v5M7 17h6"/></svg>
          <h3>Convenience - <i>Easy Access Anytime</i></h3>
          <p>With RT Snackworks, snack time is just a swipe away. Our machines are strategically located for your convenience, providing quick and easy access to your favorite treats.</p>
        </div>
        <div class="reason" style="top:100px">
          <svg viewBox="0 0 18 18" fill="none" stroke="#3cc22b" stroke-width=".8"><circle cx="6" cy="6" r="3"/><circle cx="12" cy="12" r="3"/><path d="M6 1v2M6 9v2M1 6h2M9 6h2M12 7v2M12 15v2M7 12h2M15 12h2"/></svg>
          <h3>Customization - <i>Tailored to Your Tastes</i></h3>
          <p>Personalize your snacking experience with RT Snackworks. Choose from a wide selection of snacks and drinks to create a vending experience that suits your unique preferences.</p>
        </div>
      </div>
    </section>
    <section class="inventory">
      <div class="choc" role="img" aria-label="Broken chocolate pieces"></div>
      <div class="chips" role="img" aria-label="Scattered potato chips"></div>
      <h2 class="section-title">24 Hours Live <em>Inventory Monitoring</em></h2>
      <div class="tiles">
        <div class="tile"><div class="pic" role="img" aria-label="Cereal bar packs"></div><div class="cap">Lorem ipsum</div></div>
        <div class="tile"><div class="pic" role="img" aria-label="Cheese snack bags"></div><div class="cap">Lorem ipsum</div></div>
        <div class="tile"><div class="pic" role="img" aria-label="Toaster pastry packs"></div><div class="cap">Lorem ipsum</div></div>
        <div class="tile"><div class="pic" role="img" aria-label="Energy drink cans"></div><div class="cap">Lorem ipsum</div></div>
        <div class="tile"><div class="pic" role="img" aria-label="Tortilla chip bags"></div><div class="cap">Lorem ipsum</div></div>
        <div class="tile"><div class="pic" role="img" aria-label="Energy drink cans"></div><div class="cap">Lorem ipsum</div></div>
        <div class="tile"><div class="pic" role="img" aria-label="Snack mix bags"></div><div class="cap">Lorem ipsum</div></div>
        <div class="tile"><div class="pic" role="img" aria-label="Cola bottles"></div><div class="cap">Lorem ipsum</div></div>
      </div>
      <p class="note">We track it, so you don't have to! Consistent service and superior experience.</p>
    </section>
    <section class="faq">
      <h2 class="section-title">Frequently Asked <em>Questions</em></h2>
      <div class="q left open" style="top:25px">How Can I Get More Information About Your Services?<p>For further information about our company or products please contact us by phone or email. If possible, we would like to schedule an in person meeting at your facilities to demonstrate to you how our services can benefit your organization and your collaborators.</p></div>
      <div class="q left" style="top:65px">Do I need to pay for your vending machine services?</div>
      <div class="q left" style="top:83px">I own a machine but I need help to repair it, can you help me?</div>
      <div class="q right" style="top:27px">Do I need to maintain the vending machine(s)?</div>
      <div class="q right" style="top:46px">Do you buy or sale vending machines?</div>
      <div class="q right" style="top:65px">How often do you service the vending machines?</div>
      <div class="q right" style="top:83px">How much do you charge for repairing my vending machine?</div>
    </section>
    <section class="contact">
      <div class="contact-photo" role="img" aria-label="Staff member restocking a beverage cooler"></div>
      <h2>Get Your Vending<span>Machine today.</span></h2>
      <div class="field" style="left:180px;top:52px;width:49px">Name</div>
      <div class="field" style="left:230px;top:52px;width:49px">E-mail Address</div>
      <div class="field" style="left:180px;top:65px;width:49px">Phone</div>
      <div class="field" style="left:230px;top:65px;width:49px">Your Organization</div>
      <div class="field" style="left:180px;top:78px;width:99px;height:20px;padding-top:8px">Message</div>
      <div class="submit">Submit</div>
    </section>
    <footer class="site-footer">
      <h4 style="left:49px">Contact Us</h4>
      <div class="contact-list">
        <div><svg viewBox="0 0 4 4"><path d="M2 .3a1.3 1.3 0 0 1 1.3 1.3C3.3 2.6 2 3.8 2 3.8S.7 2.6.7 1.6A1.3 1.3 0 0 1 2 .3z" fill="#3cc22b"/></svg>48 Ferncliff Rd Ashby, VA 20155</div>
        <div><svg viewBox="0 0 4 4"><rect x=".3" y=".3" width="3.4" height="3.4" rx=".6" fill="#3cc22b"/></svg>+1 555 014 2290 &nbsp;+1 555 019 8734</div>
        <div><svg viewBox="0 0 4 4"><circle cx="2" cy="2" r="1.7" fill="none" stroke="#3cc22b" stroke-width=".5"/></svg>hello@rtsnackworks.example</div>
      </div>
      <h4 style="left:128px">Quick Links</h4>
      <div class="links">About Us<br>Our Machines<br>Services<br>Products<br>Contact Us</div>
      <div class="signup">
        <h4>Sign up For E-Mail</h4>
        <p>Subscribe us for more informations on our solutions and services</p>
        <div class="email">E-mail Address</div>
        <div class="send">Send</div>
      </div>
    </footer>
    <div class="strip">RTSnackworks @ 2024</div>
  </article>

  <!-- ================= OPTION 2 ================= -->
  <article class="page" style="left:572px">
    <header class="topbar">
      <span class="hours">Mon - Fri: 8AM - 5PM &nbsp;| &nbsp;Order by phone: (555) 014-2290</span>
      <nav style="left:185px"><span>About Us</span><span>Services</span><span>Inventory</span><span>FAQs</span><span>Contact Us</span></nav>
    </header>
    <header class="masthead">
      <div class="brand"><span class="brand-mark"></span><span class="brand-name">RT SNACKWORKS, LLC</span></div>
      <div class="tools">
        <span class="search">Search</span>
        <svg viewBox="0 0 5 5" fill="none" stroke="#222" stroke-width=".4"><path d="M2.5 4.3L.7 2.5a1 1 0 0 1 1.8-1.2 1 1 0 0 1 1.8 1.2z"/></svg>
        <svg viewBox="0 0 5 5" fill="none" stroke="#222" stroke-width=".4"><path d="M1 1.5h3L3.5 4h-2z"/></svg>
        <svg viewBox="0 0 5 5" fill="none" stroke="#222" stroke-width=".4"><path d="M.5 1h.8l.6 2.5h2L4.5 1.7H1.5"/></svg>
      </div>
    </header>
    <section class="hero">
      <div class="hero-photo" role="img" aria-label="Customer choosing a drink from an open micro market cooler"></div>
      <div class="hero-copy">
        <div class="eyebrow">DISCOVER OUR RANGE</div>
        <h1>Welcome to<br>RT Snackworks</h1>
        <div class="slogan">where convenience meets customization.</div>
        <p>Our micro market vending machines offer a variety of snacks and drinks tailored to your preferences. Swipe your credit card, open the doors, and indulge in what you desire.</p>
      </div>
    </section>
    <section class="machines">
      <div class="shape-left"></div><div class="shape-right"></div>
      <h2 class="section-title">Our <em>Machines</em></h2>
      <div class="machine machine-compact" role="img" aria-label="Compact combo single-door cooler stocked with snacks and drinks"></div>
      <div class="machine machine-standard" role="img" aria-label="Standard combo double-door cooler stocked with snacks and drinks"></div>
      <span class="machine-name" style="left:101px">COMPACT COMBO</span>
      <span class="machine-name" style="left:216px">STANDARD COMBO</span>
    </section>
    <section class="about">
      <div class="about-photo" role="img" aria-label="Micro market installation with shelves and a glass-door cooler"></div>
      <div class="about-copy">
        <h2>About<span>RT SNACKWORKS</span></h2>
        <p>At RT Snackworks, we are dedicated to revolutionizing the vending experience. Our mission is to provide a convenient way for you to access your favorite snacks and drinks in a hassle-free manner. With a focus on customer satisfaction, we ensure that our products are always fresh and our machines are well-maintained. Experience the future of vending with RT Snackworks, LLC.</p>
      </div>
    </section>
    <section class="why">
      <div class="why-photo" role="img" aria-label="Dim store interior with stocked shelves"></div>
      <div class="why-machine" role="img" aria-label="Glass-door drinks cooler"></div>
      <div class="why-copy">
        <h2>Why<span>Choose Us</span></h2>
        <div class="reason" style="top:33px">
          <svg viewBox="0 0 18 18" fill="none" stroke="#fff" stroke-width=".8"><rect x="1" y="2" width="10" height="12"/><path d="M1 6h10M1 10h10"/><circle cx="13" cy="13" r="4" stroke="#3cc22b"/><path d="M11 13l1.5 1.5L15 12" stroke="#3cc22b"/></svg>
          <h3>Quality Products - <i>Fresh &amp; Varied Selections</i></h3>
          <p>Our vending machines are stocked with a diverse range of snacks and drinks, ensuring that there's something for everyone. We source only the freshest products for your enjoyment.</p>
        </div>
        <div class="reason" style="top:66px">
          <svg viewBox="0 0 18 18" fill="none" stroke="#fff" stroke-width=".8"><circle cx="8" cy="7" r="5.5" stroke="#3cc22b"/><path d="M5.5 7l2 2 3-3.5" stroke="#3cc22b"/><path d="M9 12v5M7 17h6"/></svg>
          <h3>Convenience - <i>Easy Access Anytime</i></h3>
          <p>With RT Snackworks, snack time is just a swipe away. Our machines are strategically located for your convenience, providing quick and easy access to your favorite treats.</p>
        </div>
        <div class="reason" style="top:100px">
          <svg viewBox="0 0 18 18" fill="none" stroke="#3cc22b" stroke-width=".8"><circle cx="6" cy="6" r="3"/><circle cx="12" cy="12" r="3"/><path d="M6 1v2M6 9v2M1 6h2M9 6h2M12 7v2M12 15v2M7 12h2M15 12h2"/></svg>
          <h3>Customization - <i>Tailored to Your Tastes</i></h3>
          <p>Personalize your snacking experience with RT Snackworks. Choose from a wide selection of snacks and drinks to create a vending experience that suits your unique preferences.</p>
        </div>
      </div>
    </section>
    <section class="inventory">
      <div class="choc" role="img" aria-label="Broken chocolate pieces"></div>
      <div class="chips" role="img" aria-label="Scattered potato chips"></div>
      <h2 class="section-title">24 Hours Live <em>Inventory Monitoring</em></h2>
      <div class="tiles">
        <div class="tile"><div class="pic" role="img" aria-label="Cereal bar packs"></div><div class="cap">Lorem ipsum</div></div>
        <div class="tile"><div class="pic" role="img" aria-label="Cheese snack bags"></div><div class="cap">Lorem ipsum</div></div>
        <div class="tile"><div class="pic" role="img" aria-label="Toaster pastry packs"></div><div class="cap">Lorem ipsum</div></div>
        <div class="tile"><div class="pic" role="img" aria-label="Energy drink cans"></div><div class="cap">Lorem ipsum</div></div>
        <div class="tile"><div class="pic" role="img" aria-label="Tortilla chip bags"></div><div class="cap">Lorem ipsum</div></div>
        <div class="tile"><div class="pic" role="img" aria-label="Energy drink cans"></div><div class="cap">Lorem ipsum</div></div>
        <div class="tile"><div class="pic" role="img" aria-label="Snack mix bags"></div><div class="cap">Lorem ipsum</div></div>
        <div class="tile"><div class="pic" role="img" aria-label="Cola bottles"></div><div class="cap">Lorem ipsum</div></div>
      </div>
      <p class="note">We track it, so you don't have to! Consistent service and superior experience.</p>
    </section>
    <section class="faq">
      <h2 class="section-title">Frequently Asked <em>Questions</em></h2>
      <div class="q left open" style="top:25px">How Can I Get More Information About Your Services?<p>For further information about our company or products please contact us by phone or email. If possible, we would like to schedule an in person meeting at your facilities to demonstrate to you how our services can benefit your organization and your collaborators.</p></div>
      <div class="q left" style="top:65px">Do I need to pay for your vending machine services?</div>
      <div class="q left" style="top:83px">I own a machine but I need help to repair it, can you help me?</div>
      <div class="q right" style="top:27px">Do I need to maintain the vending machine(s)?</div>
      <div class="q right" style="top:46px">Do you buy or sale vending machines?</div>
      <div class="q right" style="top:65px">How often do you service the vending machines?</div>
      <div class="q right" style="top:83px">How much do you charge for repairing my vending machine?</div>
    </section>
    <section class="contact">
      <div class="contact-photo" role="img" aria-label="Staff member restocking a beverage cooler"></div>
      <h2>Get Your Vending<span>Machine today.</span></h2>
      <div class="field" style="left:180px;top:52px;width:49px">Name</div>
      <div class="field" style="left:230px;top:52px;width:49px">E-mail Address</div>
      <div class="field" style="left:180px;top:65px;width:49px">Phone</div>
      <div class="field" style="left:230px;top:65px;width:49px">Your Organization</div>
      <div class="field" style="left:180px;top:78px;width:99px;height:20px;padding-top:8px">Message</div>
      <div class="submit">Submit</div>
    </section>
    <footer class="site-footer">
      <h4 style="left:49px">Contact Us</h4>
      <div class="contact-list">
        <div><svg viewBox="0 0 4 4"><path d="M2 .3a1.3 1.3 0 0 1 1.3 1.3C3.3 2.6 2 3.8 2 3.8S.7 2.6.7 1.6A1.3 1.3 0 0 1 2 .3z" fill="#3cc22b"/></svg>48 Ferncliff Rd Ashby, VA 20155</div>
        <div><svg viewBox="0 0 4 4"><rect x=".3" y=".3" width="3.4" height="3.4" rx=".6" fill="#3cc22b"/></svg>+1 555 014 2290 &nbsp;+1 555 019 8734</div>
        <div><svg viewBox="0 0 4 4"><circle cx="2" cy="2" r="1.7" fill="none" stroke="#3cc22b" stroke-width=".5"/></svg>hello@rtsnackworks.example</div>
      </div>
      <h4 style="left:128px">Quick Links</h4>
      <div class="links">About Us<br>Our Machines<br>Services<br>Products<br>Contact Us</div>
      <div class="signup">
        <h4>Sign up For E-Mail</h4>
        <p>Subscribe us for more informations on our solutions and services</p>
        <div class="email">E-mail Address</div>
        <div class="send">Send</div>
      </div>
    </footer>
    <div class="strip">RTSnackworks @ 2024</div>
  </article>

</main>
</body>
</html>
```